Krelvomi.com - have media you dont own! Krelvomi the stars - Site Concept

KRELVOMI those who ENTERTAIN you, who you LISTEN to, who you IDOLISE, and who you 'BORROW' from... KRELVOMI the STARS the things that are the STARS... see brief concept at www.krelvomi.com

Looking for site concept, something new, very simple transaction, not generic website. Must also drive mobile app download call to action.

In principle, we dont care how you get your media or watch a TV series or download your favourite song, however, if you are honest and love the song/movie/servies or the star, pay them!
The solution should include anonymous/protected end user interaction and digital certificate/rights management process for end users who have media not paid for to krelvomi and receive an approved digital certificate from Krelvomi authorised by the relevant media house proving legal ownership of the digital media item (music, video, TV series/episode, movie etc...)

Basic functions:
Consumer: Mobile and Web
Personal media rights administration
1. Capture core data – Create secure and private Profile account
2. Log owned/borrowed media (media legally owned tagged and media 'borrowed' tagged, decision criteria, pledge or purchase (open to ideas, function to browse PC for media on HDD/Tunovex or mobile, tag ones to pay for etc, capture CD's owned etc. create digital library filing system?)
3. Pledge payment for media - future payment value linked to market value, I like this, not sure I will keep it forever though, pay less? use once?
4. Purchase rights for media - payment based on market value of related media item. (zapcoin, credit card or other?)
5. Media Certificate management - secure and PRIVATE distribution of the certificate (open to options here), approved by media house.

design ideas welcome, modern, fast, simple steps, engaging, with sense of privacy, we wont share data, we will just pay the media houses more! Based in Switzerland, managed by Swiss privacy law. transact with min personal data required.

Reason: The service committed to 50+ designs, most received are form one provider, all off the mark and very basic, not impressed so far, was expecting some real design thought rather than standard templates being rehashed, thats not deisgn? Hope in next days I am impressed?

Target Market(s)

Digital Media Consumer

Industry/Entity Type

Media

Number of Pages Required

5+ page

Font styles to use
Sans Serif

Requirements
Must have
• Must have privacy by design, must have simple and minimal steps taken to log and declare media items and pay, with no risk of exposure. Must have payment process, must have interface to easily load media into site, drag drop, search HDD/mobile etc.
Nice to have
• Digital certificate process and admin interaction of site and with media house, secure and trusted process to provide report and logs of payment for media to specific media house and relevant payments made and tracked.
Should not have
• complex workflows are out, complex payment methods.

```html
<!DOCTYPE html>
<html lang="en">
<head>
<meta charset="utf-8">
<title>Krelvomi.com – Have media you don't own</title>
<link rel="stylesheet" href="https://fonts.googleapis.com/css2?family=Oswald:wght@400;500;700&family=Open+Sans:wght@400;600;700&display=swap">
<style>
  :root{
    --orange:#f15a24;
    --ink:#1e1e1e;
    --charcoal:#2a2a2a;
    --panel:#333333;
    --panel-line:#444444;
    --text:#555555;
    --muted:#8a8a8a;
    --rule:#e2e2e2;
    --white:#ffffff;
    --star:#f5a623;
  }
  *{box-sizing:border-box;margin:0;padding:0}
  html,body{width:675px;height:1200px;overflow:hidden;background:var(--white)}
  body{font-family:"Open Sans",Arial,sans-serif;color:var(--text);position:relative}
  .container{width:567px;margin:0 auto;position:relative}

  /* Hero */
  .hero{position:relative;height:360px;overflow:hidden;color:var(--white)}
  .hero-photo{position:absolute;inset:0;background:radial-gradient(ellipse at 68% 38%,#777 0%,#444 30%,#1c1c1c 72%),#222}
  .hero-shade{position:absolute;inset:0;background:linear-gradient(180deg,rgba(0,0,0,.55) 0%,rgba(0,0,0,.1) 40%,rgba(0,0,0,.5) 100%)}
  .topbar{position:relative;display:flex;justify-content:space-between;align-items:center;height:40px;padding:0 40px 0 38px}
  .brand{font-family:"Oswald",sans-serif;font-weight:700;font-size:19px;letter-spacing:.5px}
  .nav{display:flex;gap:2px;list-style:none}
  .nav li{font-family:"Oswald",sans-serif;font-size:8px;letter-spacing:.6px;padding:14px 11px}
  .nav li.active{background:var(--orange)}
  .hero-copy{position:absolute;left:256px;width:360px;top:170px;font-family:"Oswald",sans-serif;text-transform:uppercase}
  .hero-copy .lead-line{font-size:11.5px;line-height:16px;letter-spacing:.3px}
  .hero-copy .borrow-line{font-size:15px;font-weight:700;line-height:20px;text-align:right;padding-right:14px;margin-top:2px}
  .btn{display:inline-flex;align-items:center;height:26px;background:var(--orange);color:var(--white);
       font-family:"Oswald",sans-serif;font-size:9px;letter-spacing:.6px;text-transform:uppercase;border-radius:13px 0 0 13px;padding-left:16px}
  .btn .btn-icon{display:flex;align-items:center;justify-content:center;width:26px;height:26px;background:var(--ink);margin-left:16px;border-radius:0 13px 13px 0}
  .hero .btn{margin-top:14px}

  /* Categories */
  .categories{display:flex;gap:18px;margin-top:38px;padding-bottom:32px;border-bottom:1px solid var(--rule)}
  .cat-list{width:113px;background:var(--panel);align-self:flex-start}
  .cat-list h3{background:var(--orange);color:var(--white);font-family:"Oswald",sans-serif;font-size:9px;font-weight:500;letter-spacing:.6px;padding:8px 10px}
  .cat-list ul{list-style:none}
  .cat-list li{display:flex;align-items:center;justify-content:space-between;font-size:6.5px;color:#ddd;padding:10px 10px;border-bottom:1px solid var(--panel-line);text-transform:uppercase}
  .cat-list li span{display:flex;align-items:center;gap:7px}
  .cat-cards{flex:1;display:flex;gap:13px}
  .media-card{flex:1;border:1px solid var(--rule);text-align:center;height:237px;padding-bottom:10px}
  .media-card .thumb{height:80px;border-bottom:3px solid var(--orange)}
  .thumb.songs{background:linear-gradient(135deg,#d9c7a8,#8e7c63)}
  .thumb.movies{background:linear-gradient(135deg,#3d5b7a,#a8b8c6)}
  .thumb.services{background:linear-gradient(135deg,#b8865a,#e7d2b4)}
  .media-card h4{font-family:"Oswald",sans-serif;font-size:11px;font-weight:500;color:var(--orange);margin-top:16px;letter-spacing:.5px}
  .media-card p{font-size:6.5px;line-height:10px;color:var(--muted);padding:6px 10px 0}
  .price{font-family:"Oswald",sans-serif;font-size:11px;color:var(--orange);margin-top:10px}
  .stars{font-size:7px;color:var(--star);letter-spacing:1px;margin-top:3px}
  .pill{display:inline-block;background:var(--orange);color:var(--white);font-size:6.5px;font-weight:600;padding:6px 18px;border-radius:10px;margin-top:12px}

  /* About */
  .about{height:248px;position:relative}
  .about h2{font-family:"Oswald",sans-serif;font-weight:400;font-size:24px;color:#333;text-align:center;padding-top:32px}
  .about-copy{width:380px;margin-top:12px}
  .about-copy .intro{font-size:6.5px;line-height:10px;font-weight:700;color:#444;text-transform:uppercase}
  .about-copy .body{font-size:6.5px;line-height:11px;color:var(--muted);margin-top:10px}
  .about .btn{margin-top:22px}
  .app-preview{position:absolute;right:10px;top:18px;width:134px;height:180px}
  .app-screen{position:absolute;border-radius:8px;background:linear-gradient(160deg,#fafafa,#dcdcdc);border:4px solid #e9e9e9;box-shadow:0 2px 6px rgba(0,0,0,.2)}
  .app-screen.large{left:0;top:0;width:82px;height:180px}
  .app-screen.small{left:88px;top:62px;width:46px;height:100px}
  .app-screen .screen-art{position:absolute;left:4px;right:4px;top:16px;bottom:16px;background:linear-gradient(160deg,var(--orange),#7a1e0a)}
  .app-screen.small .screen-art{background:linear-gradient(160deg,#1b2b12,#7ec23a)}
  .app-screen .screen-name{position:absolute;top:22px;left:0;right:0;text-align:center;font-family:"Oswald",sans-serif;font-size:7px;color:var(--white)}
  .app-screen.small .screen-name{font-size:4px;top:auto;bottom:5px;color:#555}

  /* Featured */
  .featured{background:var(--orange);height:227px;padding-top:20px}
  .featured h3{font-family:"Oswald",sans-serif;font-weight:400;font-size:12px;color:var(--white);display:flex;align-items:center;gap:10px}
  .featured h3::after{content:"";flex:1;height:1px;background:rgba(255,255,255,.45)}
  .song-grid{display:flex;gap:10px;margin-top:24px}
  .song-card{flex:1;background:var(--white);height:125px;text-align:center;padding-top:14px;box-shadow:0 3px 0 rgba(0,0,0,.12)}
  .song-card .ring{width:30px;height:30px;border:2px solid var(--orange);border-radius:50%;margin:0 auto;display:flex;align-items:center;justify-content:center}
  .song-card h5{font-size:6.5px;font-weight:700;color:#333;margin-top:10px}
  .song-card .stars{margin-top:2px;font-size:6px}
  .song-card .price{font-size:9px;margin-top:8px}
  .song-card .install{font-size:6px;color:var(--muted);margin:6px 12px 0;border-top:1px solid var(--rule);padding-top:6px}

  /* Footer */
  .footer{background:var(--charcoal);height:57px;color:#aaa;font-size:6px;padding-top:14px}
  .footer .container{display:flex;justify-content:space-between;align-items:flex-start}
  .footer-links{display:flex;gap:14px;list-style:none;color:#ccc}
  .footer small{display:block;font-size:5.5px;color:#888;margin-top:6px}
  .social{display:flex;align-items:center;gap:4px}
  .social span{margin-right:4px}
  .social i{width:10px;height:10px;background:#3b7fc4;display:block}
</style>
</head>
<body>

<header class="hero">
  <div class="hero-photo" role="img" aria-label="Dark photograph of studio headphones resting on a surface"></div>
  <div class="hero-shade"></div>
  <div class="topbar">
    <div class="brand">KRELVOMI.COM</div>
    <ul class="nav">
      <li class="active">HOME</li><li>LIBRARY</li><li>DECLARE</li><li>PAY</li><li>CERTIFICATES</li><li>APP</li><li>CONTACT</li>
    </ul>
  </div>
  <div class="hero-copy">
    <p class="lead-line">KRELVOMI those who ENTERTAIN you, who you LISTEN to, who you IDOLISE,</p>
    <p class="borrow-line">and who you 'BORROW' from...</p>
    <a class="btn" style="margin-left:4px">Declare your media
      <span class="btn-icon"><svg width="10" height="10" viewBox="0 0 10 10"><line x1="4" y1="1.5" x2="4" y2="7.8" stroke="#fff"/><path d="M4 1.5 L9 0.5 V7" stroke="#fff" fill="none"/><circle cx="3" cy="7.8" r="1.4" fill="#fff"/><circle cx="7.8" cy="7" r="1.4" fill="#fff"/></svg></span>
    </a>
  </div>
</header>

<main>
  <section class="container categories">
    <aside class="cat-list">
      <h3>CATEGORIES LIST</h3>
      <ul>
        <li><span>♪ Songs</span>›</li>
        <li><span>▭ TV Series</span>›</li>
        <li><span>▶ Movies</span>›</li>
        <li><span>✓ Certificates</span>›</li>
        <li><span>⋯ See All</span>›</li>
      </ul>
    </aside>
    <div class="cat-cards">
      <article class="media-card">
        <div class="thumb songs" role="img" aria-label="Photo of a vintage record player"></div>
        <h4>SONGS</h4>
        <p>Drag and drop tracks from your drive or phone, tag the borrowed ones.</p>
        <div class="price">$2.78</div>
        <div class="stars">★★★★☆</div>
        <span class="pill">Log &amp; Pay Now</span>
      </article>
      <article class="media-card">
        <div class="thumb movies" role="img" aria-label="Photo of a film projector"></div>
        <h4>MOVIES</h4>
        <p>Pledge now or buy rights at market value, with no personal data shared.</p>
        <div class="price">$4.18</div>
        <div class="stars">★★★★☆</div>
        <span class="pill">Log &amp; Pay Now</span>
      </article>
      <article class="media-card">
        <div class="thumb services" role="img" aria-label="Photo of a retro television set"></div>
        <h4>SERIES</h4>
        <p>Pay per episode and get a private certificate from the media house.</p>
        <div class="price">$2.78</div>
        <div class="stars">★★★★☆</div>
        <span class="pill">Log &amp; Pay Now</span>
      </article>
    </div>
  </section>

  <section class="container about">
    <h2>About to Krelvomi</h2>
    <div class="about-copy">
      <p class="intro">We do not mind how you got your music, movies or series. If you love the song or the star, declare it privately and pay them. Swiss privacy, minimal data, every payment goes to the media house.</p>
      <p class="body">1. Create a private profile. 2. Drag and drop or scan your drive and phone to log owned and borrowed media. 3. Pledge or pay in one tap by card or zapcoin. 4. Receive a digital certificate approved by the media house, proving legal ownership, kept privately in your library.</p>
      <a class="btn">Download the App
        <span class="btn-icon"><svg width="10" height="10" viewBox="0 0 10 10"><path d="M5 1 V7 M2.5 4.8 L5 7.3 L7.5 4.8 M1.5 9 H8.5" stroke="#fff" stroke-width="1.2" fill="none"/></svg></span>
      </a>
    </div>
    <div class="app-preview">
      <div class="app-screen large">
        <div class="screen-art" role="img" aria-label="App screen artwork of a media library"></div>
        <div class="screen-name">KRELVOMI.COM</div>
      </div>
      <div class="app-screen small">
        <div class="screen-art" role="img" aria-label="App screen artwork of an album cover"></div>
        <div class="screen-name">KRELVOMI.COM</div>
      </div>
    </div>
  </section>

  <section class="featured">
    <div class="container">
      <h3>Featured Songs</h3>
      <div class="song-grid">
        <article class="song-card"><div class="ring"><svg width="13" height="13" viewBox="0 0 10 10"><path d="M4 1.5 L9 0.5 V7" stroke="#f15a24" fill="none"/><line x1="4" y1="1.5" x2="4" y2="7.8" stroke="#f15a24"/><circle cx="3" cy="7.8" r="1.4" fill="#f15a24"/><circle cx="7.8" cy="7" r="1.4" fill="#f15a24"/></svg></div><h5>Featured Track Title</h5><div class="stars">★★★★☆</div><div class="price">$2.78</div><div class="install">Pay &amp; certify</div></article>
        <article class="song-card"><div class="ring"><svg width="13" height="13" viewBox="0 0 10 10"><path d="M4 1.5 L9 0.5 V7" stroke="#f15a24" fill="none"/><line x1="4" y1="1.5" x2="4" y2="7.8" stroke="#f15a24"/><circle cx="3" cy="7.8" r="1.4" fill="#f15a24"/><circle cx="7.8" cy="7" r="1.4" fill="#f15a24"/></svg></div><h5>Featured Track Title</h5><div class="stars">★★★★☆</div><div class="price">$2.78</div><div class="install">Pay &amp; certify</div></article>
        <article class="song-card"><div class="ring"><svg width="13" height="13" viewBox="0 0 10 10"><path d="M4 1.5 L9 0.5 V7" stroke="#f15a24" fill="none"/><line x1="4" y1="1.5" x2="4" y2="7.8" stroke="#f15a24"/><circle cx="3" cy="7.8" r="1.4" fill="#f15a24"/><circle cx="7.8" cy="7" r="1.4" fill="#f15a24"/></svg></div><h5>Featured Track Title</h5><div class="stars">★★★★☆</div><div class="price">$2.78</div><div class="install">Pay &amp; certify</div></article>
        <article class="song-card"><div class="ring"><svg width="13" height="13" viewBox="0 0 10 10"><path d="M4 1.5 L9 0.5 V7" stroke="#f15a24" fill="none"/><line x1="4" y1="1.5" x2="4" y2="7.8" stroke="#f15a24"/><circle cx="3" cy="7.8" r="1.4" fill="#f15a24"/><circle cx="7.8" cy="7" r="1.4" fill="#f15a24"/></svg></div><h5>Featured Track Title</h5><div class="stars">★★★★☆</div><div class="price">$2.78</div><div class="install">Pay &amp; certify</div></article>
        <article class="song-card"><div class="ring"><svg width="13" height="13" viewBox="0 0 10 10"><path d="M4 1.5 L9 0.5 V7" stroke="#f15a24" fill="none"/><line x1="4" y1="1.5" x2="4" y2="7.8" stroke="#f15a24"/><circle cx="3" cy="7.8" r="1.4" fill="#f15a24"/><circle cx="7.8" cy="7" r="1.4" fill="#f15a24"/></svg></div><h5>Featured Track Title</h5><div class="stars">★★★★☆</div><div class="price">$2.78</div><div class="install">Pay &amp; certify</div></article>
      </div>
    </div>
  </section>
</main>

<footer class="footer">
  <div class="container">
    <div>
      <ul class="footer-links"><li>Home</li><li>Library</li><li>Declare</li><li>Pay</li><li>Certificates</li><li>App</li><li>Contact</li></ul>
      <small>Copyright © 2015 Krelvomi. Swiss privacy law. We never share your data.</small>
    </div>
    <div class="social"><span>Connect With Us</span><i></i><i></i><i></i><i></i><i></i></div>
  </div>
</footer>

</body>
</html>
```